KLORA product web page

We need a new web design for our KLORA product page. You can find more information about the project on the current web site - www.klora.example

What we need from a new design (uncoded):
- landing pages + template
- all information on one page
- the design should be focused on the product - light bulb + app
- web site should be with some dynamics like a background with parallax effect in the current version
- fonts should be chosen
- a number of illustrations should be designed

Here is schema for a new design: https://files.examplehost.net/d/draw-7QpX2mLk9RtYv4Hs/edit

Here is a document with all texts for a new design: https://files.examplehost.net/d/doc-3WnZ8bJf5KcUe1Ga/edit

Illustrations to use:
v1 - https://files.examplehost.net/f/fold-A1kT9pQw2ZxR
v2 - https://files.examplehost.net/f/fold-B7mH4sLv6YcN

PearOS screens: https://files.examplehost.net/f/fold-C3rJ8dKe1WuP

KLORA logo: https://files.examplehost.net/f/fold-D5nF2gTb9XoM
Updates

I forgot to add the definition text "KLORA - is.." to the document with texts. Sorry, my mistake.

Target Market(s)

25-45 year old adults who are interested in "smart" devices for their health.

Industry/Entity Type

Brintel

Colors

Designer to choose colors to be used in the design.

Requirements
Must have
• - landing pages + template
- fonts should be chosen

```html
<!DOCTYPE html>
<html lang="en">
<head>
<meta charset="utf-8">
<title>KLORA — Smart Light</title>
<link rel="stylesheet" href="https://fonts.googleapis.com/css2?family=Oxygen:wght@300;400;700&display=swap">
<style>
:root{
  --header:#6ec6d7;
  --teal-btn:#2cc3dc;
  --dark:#1e2a2e;
  --band:rgba(38,48,50,.86);
  --text-grey:#5a5a5a;
  --title:#2b2b2b;
  --yellow:#fdb300;
  --purple:#663399;
  --blue:#4fb6cf;
  --blue-btn:#2b97b4;
  --footer:#f6f6f6;
  --white:#ffffff;
}
*{margin:0;padding:0;box-sizing:border-box}
html,body{width:1200px;height:2439px;overflow:hidden}
body{position:relative;font-family:"Oxygen",sans-serif;color:var(--text-grey);background:var(--white)}

/* header */
.site-header{position:absolute;left:0;top:0;width:1200px;height:104px;background:var(--header)}
.brand{position:absolute;left:101px;top:28px;font-size:38px;font-weight:400;letter-spacing:4px;color:var(--white);line-height:48px}
.main-nav{position:absolute;top:44px;left:0;width:1200px}
.main-nav a{position:absolute;color:var(--white);font-size:17px;font-weight:700;text-decoration:none}

/* hero */
.hero-visual{position:absolute;left:0;top:104px;width:1200px;height:598px;
  background:linear-gradient(180deg,#a9c6d9 0%,#8fb2c9 40%,#a2b4bc 62%,#b39c82 75%,#8f6f53 100%)}
.hero-copy{position:absolute;left:93px;top:238px;color:var(--white)}
.hero-title{font-size:44px;font-weight:400;line-height:54px}
.hero-sub{margin-top:10px;font-size:22px;font-weight:300;line-height:31px;width:490px}
.btn{position:absolute;height:36px;line-height:36px;text-align:center;font-size:15px;color:var(--white);border-radius:2px}
.btn-preorder{left:96px;top:379px;width:137px;background:var(--teal-btn)}
.btn-more{left:237px;top:379px;width:139px;background:var(--dark)}
.slider-dots{position:absolute;left:98px;top:436px;display:flex;gap:3px}
.slider-dots span{width:15px;height:15px;border-radius:50%;background:var(--white)}
.hero-band{position:absolute;left:0;top:598px;width:1200px;height:104px;background:var(--band);color:var(--white);padding:33px 0 0 94px;font-size:24px;font-weight:300}
.hero-band strong{font-size:32px;font-weight:400}

/* shared */
.section-title{font-size:34px;font-weight:400;line-height:44px}
.body-text{font-size:13px;line-height:22.5px}
.next-tab{position:absolute;left:550px;width:100px;height:38px;border-radius:50px 50px 0 0;text-align:center;line-height:42px;color:var(--white);font-size:17px}

/* app & color */
.app-section{position:absolute;left:0;top:702px;width:1200px;height:412px;background:var(--white)}
.app-section .section-title{position:absolute;left:88px;top:63px;color:var(--title)}
.app-copy{position:absolute;left:88px;top:118px;width:685px;color:var(--text-grey)}
.app-copy p+p{margin-top:15px}
.bulb-visual{position:absolute;left:850px;top:62px;width:160px;height:285px;background:#ecedee}

/* health */
.health-section{position:absolute;left:0;top:1114px;width:1200px;height:460px;background:var(--yellow);color:var(--white)}
.devices-visual{position:absolute;left:98px;top:60px;width:300px;height:309px;background:linear-gradient(180deg,#e0b040 0%,#c99a30 100%)}
.health-copy{position:absolute;left:463px;top:60px;width:662px}
.health-copy .sub-title{font-size:25px;font-weight:400;line-height:34px;margin-top:18px}
.health-copy .body-text{margin-top:2px}

/* specs */
.specs-section{position:absolute;left:0;top:1574px;width:1200px;height:454px;background:var(--purple);color:var(--white)}
.specs-copy{position:absolute;left:76px;top:66px;width:780px}
.specs-lead{font-size:15px;margin-top:10px;line-height:24px}
.specs-copy .body-text{margin-top:7px;line-height:24px}
.compat-title{font-size:17px;font-weight:400;margin-top:16px;line-height:26px}
.compat-list{list-style:none;font-size:12.5px;line-height:22.5px;margin-top:4px}
.round-visual{position:absolute;border-radius:50%;border:4px solid var(--white)}
.specs-visual{left:850px;top:93px;width:260px;height:260px;background:linear-gradient(180deg,#4a4a3c 0%,#33342f 100%)}

/* pre-order */
.preorder-section{position:absolute;left:0;top:2028px;width:1200px;height:330px;background:var(--blue);color:var(--white)}
.preorder-copy{position:absolute;left:76px;top:51px;width:640px}
.preorder-copy .body-text{margin-top:8px}
.signup{position:absolute;left:75px;top:185px;display:flex}
.signup-input{width:284px;height:42px;background:var(--white);border-radius:3px 0 0 3px;color:#8a8a8a;font-size:14px;line-height:42px;padding-left:16px}
.signup-btn{width:51px;height:42px;background:var(--blue-btn);border-radius:0 3px 3px 0;display:flex;align-items:center;justify-content:center}
.person-visual{left:813px;top:31px;width:260px;height:260px;background:#e4e4e2}

/* footer */
.site-footer{position:absolute;left:0;top:2358px;width:1200px;height:81px;background:var(--footer);font-size:12.5px;color:#666}
.footer-links{position:absolute;left:81px;top:33px}
.footer-links span{margin:0 9px;color:#999}
.social{position:absolute;left:782px;top:29px;display:flex;gap:8px}
.social span{width:20px;height:20px;border-radius:50%;background:#8a8a8a}
.copyright{position:absolute;left:873px;top:33px}
</style>
</head>
<body>

<header class="site-header">
  <div class="brand">KLORA</div>
  <nav class="main-nav">
    <a style="left:722px">Pre-Order</a>
    <a style="left:849px">Blog</a>
    <a style="left:933px">Contacts</a>
    <a style="left:1054px">RU</a>
  </nav>
</header>

<section class="hero">
  <div class="hero-visual" role="img" aria-label="Photo of a KLORA smart bulb glowing green on a wooden table against a blurred blue room"></div>
  <div class="hero-copy">
    <h1 class="hero-title">Turn your KLORA on!</h1>
    <p class="hero-sub">Create light scenes and adapt them to your needs with KLORA App.</p>
  </div>
  <a class="btn btn-preorder">Pre-order</a>
  <a class="btn btn-more">Read More</a>
  <div class="slider-dots"><span></span><span></span><span></span><span></span></div>
  <div class="hero-band"><strong>KLORA</strong> is Lorem ipsum dolor sit amet consectetuer adipiscing elit nam cursus</div>
</section>

<section class="app-section">
  <h2 class="section-title">KLORA App &amp; Color</h2>
  <div class="app-copy body-text">
    <p>KLORA Application allows you to control each lightbulb at home. Manage your lighting by creating functional groups and adding/excluding lightbulbs. Correctly matched lighting will help you work more productively and relax to the outmost. Create light scenes and adapt them to your needs. KLORA App memorizes your favorite moods, so that you can use your settings anytime. Play with million colors and adjust the brightness of your home lighting. KLORA works on PearOS 6+ and Robo OS 4+.</p>
    <p>Experiment with millions of colors! Pick any color from the screen of your mobile device and enjoy the ambience. LED lightbulb KLORA can transform conventional lighting into the night lights of Seattle or bring in the rich summer hues of Provence. Enliven your fantasies or raise your best</p>
  </div>
  <div class="bulb-visual" role="img" aria-label="Product shot of the KLORA smart lightbulb"></div>
  <div class="next-tab" style="top:374px;background:var(--yellow)">Next</div>
</section>

<section class="health-section">
  <div class="devices-visual" role="img" aria-label="Smartphone showing the KLORA app next to a KLORA lightbulb"></div>
  <div class="health-copy">
    <h2 class="section-title">KLORA and health</h2>
    <p class="body-text">Choose a scene for setting the alarm and improve your sleep naturally. KLORA lighting system creates the necessary conditions for normalizing your circadian rhythms. Set your smart lightbulbs to turn on: now you can wake up "on the sunny side" despite gloomy weather. KLORA lighting system will reduce your stress level.<br>10 preset moods provide positive impact on your health. Designed to be what your mind and body need. We developed predefined modes in accordance with physiological and psychological aspects of human activities.</p>
    <h3 class="sub-title">Lighting Design</h3>
    <p class="body-text">Wireless lightbulbs with ShortLink and MeshWave help you implement the concept of the smart home. KLORA makes it affordable. Real lighting design at your place, couldn't have been simpler.<br>Create optimal lighting for each functional area - set the perfect light for your kitchen, living room and nursery. Name individual lightbulbs or groups of them, set your color mood, pick a palette for each room. Stay informed of every smart lightbulb's condition, save your settings and load them anytime.</p>
  </div>
  <div class="next-tab" style="top:422px;background:var(--purple)">Next</div>
</section>

<section class="specs-section">
  <div class="specs-copy">
    <h2 class="section-title">KLORA technical specifications</h2>
    <p class="specs-lead">KLORA lightbulb is a 85W incandescent equivalent that transforms your visual environment.</p>
    <p class="body-text">E27 socket: no need to change anything. Easy way to home automation at hand. And yes, you can still use those switches.</p>
    <p class="body-text">12.5W (110 - 230V,50Hz), 1000lm+: energy efficient LED lightbulb KLORA shines brighter than others and saves energy.</p>
    <p class="body-text">2700-5500K: You are not limited in your choice of color temperature. Turn on warm or cold light depending on your activities.</p>
    <h3 class="compat-title">Compatibility:</h3>
    <ul class="compat-list">
      <li>Pearphone 4S/5/5C/5S</li>
      <li>Peartab 3/4/Air/mini/mini Air</li>
      <li>Pearplayer 5th generation or newer</li>
      <li>All Robo OS devices with ShortLink 2.1 or 4</li>
    </ul>
  </div>
  <div class="round-visual specs-visual" role="img" aria-label="Photo of a smartphone running the KLORA app on a dark table"></div>
  <div class="next-tab" style="top:416px;background:var(--blue)">Next</div>
</section>

<section class="preorder-section">
  <div class="preorder-copy">
    <h2 class="section-title">Pre Order</h2>
    <p class="body-text">Etiam eu urna Sed porta Suspendisse quam leo molestie sed luctus quis feugiat in pede Fusce tellus Sed metus augue convallis et vehicula ut pulvinar eu ante Integer orci tellus tristique vitae consequat nec porta vel lectus Nulla sit amet diam Duis non nunc libero a tempus libero lectus feugiat felis</p>
  </div>
  <div class="signup">
    <div class="signup-input">Email address</div>
    <div class="signup-btn">
      <svg width="22" height="16" viewBox="0 0 22 16" aria-hidden="true"><rect x="0" y="0" width="22" height="16" rx="2" fill="#fff"/><path d="M1 2 L11 9 L21 2" fill="none" stroke="#2b97b4" stroke-width="2"/></svg>
    </div>
  </div>
  <div class="round-visual person-visual" role="img" aria-label="Photo of a smiling customer sitting at a laptop"></div>
</section>

<footer class="site-footer">
  <div class="footer-links">Contact Us<span>|</span>Support<span>|</span>Term of Use</div>
  <div class="social"><span></span><span></span><span></span></div>
  <div class="copyright">© 2014 Company Name &nbsp;All right reserved</div>
</footer>

</body>
</html>
```